Luxury travel agency needs a website design

We are a travel agency specializing in booking luxury vacations. We specialize in Hawaii, Europe and Caribbean, but will do all vacations. I want a very classy website design which would attract luxury clients. The company name is "Harbors and Hammocks Travel Agency". Would love the web design to go with the color scheme of the logo. Hex codes included in files. Logo is attached. Would also love more Grey in the website. I want it very elegant

Coding

Coded - Design and coding required

Font styles to use
Sans Serif
Decorative

Requirements
Must have
• - Consultation Tab or a page where the client can fill out a short form about what vacation that they would want to book. I want this info to be sent to me in order for me to contact them.
- Somewhere with my contact info "email: marla@harborsandhammockstravel.example and phone number"
- Social media links
- About section "Marla Dunbevy - Agency Owner (picture provided)
Marla has been traveling full time for the passed two years and has been very passionate about travel from a young age. Marla is dedicated to working closely with clients to book their dream vacation.
Marla's specializations include honeymoons and anniversaries focusing on travel in Europe, Hawaii and all inclusive resorts in the Caribbean.

```html
<!DOCTYPE html>
<html lang="en">
<head>
<meta charset="utf-8">
<title>Harbors &amp; Hammocks Travel Agency</title>
<link rel="stylesheet" href="https://fonts.googleapis.com/css2?family=Work+Sans:wght@400;500;600;700;800&family=Great+Vibes&display=swap">
<style>
:root{
  --orange:#e8603c;
  --yellow:#f0b94a;
  --grey:#e1e1e3;
  --grey-light:#f1f1f1;
  --dark:#262626;
  --ink:#1b1b1b;
  --text:#333;
  --white:#fff;
  --social:#2b3e8f;
}
*{margin:0;padding:0;box-sizing:border-box}
html,body{width:1200px;height:4175px;overflow:hidden}
body{position:relative;font-family:"Work Sans",Arial,sans-serif;color:var(--text);background:var(--white)}
section,header,footer{position:absolute;left:0;width:1200px}

/* header */
.site-header{top:0;height:122px;background:var(--white)}
.brand{position:absolute;display:flex;align-items:center;gap:10px;font-weight:700;color:var(--ink)}
.brand-dot{width:34px;height:34px;border-radius:50%;background:var(--yellow);flex:none}
.brand-name{line-height:1.05;font-size:22px;letter-spacing:.5px}
.brand-name small{display:block;font-size:10px;letter-spacing:2px;font-weight:700}
.follow{position:absolute;display:flex;align-items:center;gap:8px;font-size:10px;font-weight:500;color:var(--ink)}
.follow .dot{width:27px;height:27px;border-radius:50%;background:var(--social)}
.call{position:absolute;left:910px;top:24px;display:flex;gap:14px;align-items:center}
.call p{font-size:11px;color:var(--ink);line-height:1.3}
.call strong{display:block;font-size:17px;font-weight:500}
.main-nav{position:absolute;top:84px;left:0;width:1200px;font-size:15px;font-weight:500;color:var(--ink)}
.main-nav span{position:absolute}
.main-nav .active{color:var(--orange)}
.main-nav .active::after{content:"";position:absolute;left:0;right:0;top:24px;height:3px;background:var(--orange)}

/* hero */
.hero{top:122px;height:593px;background:linear-gradient(180deg,#8d8e7f 0%,#b9ab84 18%,#4f7a64 38%,#5f8b70 55%,#2f5a2c 75%,#1e3e1c 100%)}
.hero-title{position:absolute;top:168px;width:100%;text-align:center;color:var(--white);font-size:46px;font-weight:800;letter-spacing:1px}
.hero-sub{position:absolute;top:232px;width:100%;text-align:center;color:var(--white);font-size:20px;font-weight:500}
.btn{display:inline-flex;align-items:center;justify-content:center;background:var(--orange);color:var(--white);font-weight:700}
.hero .btn{position:absolute;left:532px;top:287px;width:136px;height:45px;font-size:16px}
.dots{position:absolute;top:541px;left:562px;display:flex;gap:11px;align-items:center}
.dots i{width:6px;height:6px;border-radius:50%;background:var(--white)}
.dots i.on{width:12px;height:12px;border:2px solid var(--white);background:var(--orange)}

/* about */
.about{top:715px;height:474px}
.about-backdrop{position:absolute;left:130px;top:42px;width:384px;height:384px;border-radius:50%;background:linear-gradient(160deg,#f0b94a 0%,#ee9a45 50%,#e8603c 100%)}
.about-photo{position:absolute;left:251px;top:88px;width:344px;height:276px;background:linear-gradient(135deg,#6d6257,#a8998a 45%,#5b5046)}
.about-text{position:absolute;left:642px;top:62px;width:440px}
.eyebrow{font-size:17px;font-weight:500;color:var(--ink);display:inline-block;padding-bottom:4px;border-bottom:3px solid var(--yellow)}
.about-text h2{font-size:24px;font-weight:700;color:var(--ink);margin-top:14px}
.role{font-size:16px;margin-top:4px;color:var(--ink)}
.about-text p.bio{font-size:15px;line-height:22px;margin-top:24px;color:var(--ink)}
.about-text .btn{margin-top:28px;width:98px;height:31px;font-size:11px}

/* section headings */
.heading{position:absolute;width:100%;text-align:center;font-size:23px;font-weight:700;color:var(--ink)}
.heading::after{content:"";display:block;width:64px;height:3px;background:var(--yellow);margin:18px auto 0}

/* packages */
.packages{top:1189px;height:514px;background:var(--grey)}
.pkg{position:absolute;top:128px;width:302px;height:328px;overflow:hidden}
.pkg-label{position:absolute;top:140px;width:100%;text-align:center;color:var(--white);font-size:24px;font-weight:700;letter-spacing:.5px}
.pkg-badge{position:absolute;left:101px;top:279px;width:100px;height:100px;border-radius:50%;background:var(--white);display:flex;justify-content:center;padding-top:18px}
.pkg-hawaii{left:131px;background:linear-gradient(180deg,#1e2f5f 0%,#3a5b8a 35%,#2f6d8d 60%,#3ea3c0 100%)}
.pkg-europe{left:449px;background:linear-gradient(180deg,#a9cfe6 0%,#c8d7de 40%,#6e6b52 75%,#3c3a28 100%)}
.pkg-carib{left:766px;background:linear-gradient(180deg,#2c3f6d 0%,#e58644 30%,#f2b35a 40%,#1f8a9b 65%,#2e7c4f 100%)}

/* offers */
.offers{top:1703px;height:860px}
.tile{position:absolute;overflow:hidden;color:var(--white)}
.tile .tag{display:inline-block;background:var(--orange);color:var(--white);font-size:14px;font-weight:700;padding:2px 6px;line-height:17px}
.tile .price{display:inline-block;background:var(--yellow);color:var(--white);font-size:21px;font-weight:700;padding:2px 10px}
.tile h3{font-size:24px;font-weight:700;line-height:27px;letter-spacing:.5px}
.script{font-family:"Great Vibes",cursive;font-weight:400;font-size:48px;line-height:44px}
.tile p{font-size:14px;font-weight:500}
.t1{left:130px;top:136px;width:235px;height:329px;background:linear-gradient(180deg,#2d8fd6 0%,#61bde6 35%,#17c6c8 60%,#0b8fa0 100%)}
.t2{left:373px;top:136px;width:234px;height:329px;background:linear-gradient(180deg,#5d6f8a 0%,#b1866a 45%,#7d5a42 75%,#3f3429 100%)}
.t3{left:618px;top:136px;width:448px;height:329px;background:linear-gradient(135deg,#2c6b38 0%,#3da07a 30%,#36cfb8 55%,#1fae9f 100%)}
.t4{left:130px;top:477px;width:477px;height:331px;background:linear-gradient(180deg,#8fb7e0 0%,#c6dcef 45%,#8aa1b8 70%,#3f5c2e 100%)}
.t5{left:618px;top:477px;width:221px;height:331px;background:linear-gradient(180deg,#c9b6e0 0%,#e6c9d8 30%,#a19a93 60%,#6c665f 100%)}
.t6{left:845px;top:477px;width:221px;height:331px;background:linear-gradient(180deg,#6ea9e2 0%,#b7daf3 45%,#79d4d6 70%,#efe9dc 100%)}

/* testimonials */
.testimonials{top:2563px;height:519px;background:linear-gradient(180deg,#f3f3f4 0%,#e9e7e3 45%,#cfcabc 100%)}
.quote-card{position:absolute;top:129px;width:296px;height:336px;background:var(--white);padding:22px 34px 0 40px;box-shadow:0 1px 4px rgba(0,0,0,.06)}
.quote-mark{color:var(--yellow);font-size:30px;font-weight:700;line-height:20px;height:22px}
.quote-card p{font-size:14px;line-height:19.3px;color:var(--ink);margin-top:8px}
.quote-card .who{margin-top:22px;font-size:11px;font-weight:700;color:var(--ink);line-height:15px}
.quote-card .who span{display:block;font-weight:400}

/* features */
.features{top:3082px;height:332px;background:var(--yellow)}
.feature{position:absolute;top:51px;width:320px;text-align:center}
.feature .icon{width:108px;height:108px;border-radius:50%;background:var(--white);margin:0 auto;display:flex;align-items:center;justify-content:center}
.feature h4{font-size:15px;font-weight:700;color:var(--ink);margin-top:38px}
.feature p{font-size:13px;line-height:16px;color:var(--ink);margin-top:10px;padding:0 28px}

/* contact */
.contact{top:3414px;height:519px;background:linear-gradient(180deg,#2a2a2a,#1e1e1e)}
.contact .heading{color:var(--white)}
.field{position:absolute;background:var(--white);font-size:12px;color:var(--ink);padding:14px 18px}
.contact .btn{position:absolute;left:538px;top:420px;width:124px;height:44px;font-size:17px}

/* footer */
.site-footer{top:3933px;height:242px;background:var(--grey)}
.site-footer .brand-name{font-size:26px}
.mail{position:absolute;left:745px;top:44px;display:flex;gap:14px;align-items:flex-start;font-size:13px;color:var(--ink);line-height:18px}
.mail strong{display:block;font-size:15.5px;font-weight:500}
.footer-nav{position:absolute;top:113px;left:0;width:1200px;font-size:13px;font-weight:500;color:var(--ink)}
.footer-nav span{position:absolute}
.rule{position:absolute;left:130px;top:171px;width:938px;height:1px;background:#c8c8c8}
.copy{position:absolute;top:200px;width:100%;text-align:center;font-size:11px;color:var(--ink)}
</style>
</head>
<body>

<header class="site-header">
  <div class="brand" style="left:130px;top:38px">
    <span class="brand-dot"></span>
    <span class="brand-name">Harbors &amp; Hammocks<small>TRAVEL AGENCY</small></span>
  </div>
  <div class="follow" style="left:689px;top:30px">FOLLOW US <span class="dot" style="margin-left:4px"></span><span class="dot"></span><span class="dot"></span></div>
  <div class="call">
    <svg width="26" height="26" viewBox="0 0 24 24" fill="none" stroke="#1b1b1b" stroke-width="1.6"><path d="M5 3h4l2 5-2.5 1.5a11 11 0 0 0 6 6L16 13l5 2v4a2 2 0 0 1-2 2A17 17 0 0 1 3 5a2 2 0 0 1 2-2z"/><path d="M15 3a6 6 0 0 1 6 6M15 7a2 2 0 0 1 2 2"/></svg>
    <p>CALL US<strong>888.888.8888</strong></p>
  </div>
  <nav class="main-nav">
    <span class="active" style="left:384px">HOME</span>
    <span style="left:464px">ABOUT US</span>
    <span style="left:581px">CONSULTATION</span>
    <span style="left:733px">TOUR PACKAGES</span>
    <span style="left:900px">BLOG</span>
    <span style="left:971px">CONTACT US</span>
  </nav>
</header>

<section class="hero" role="img" aria-label="Aerial view of a tropical harbor bay with green hills and anchored sailboats">
  <h1 class="hero-title">LUXURY VACATIONS</h1>
  <p class="hero-sub">Lorem Ipsum is simply dummy text of the printing</p>
  <span class="btn">READ MORE</span>
  <div class="dots"><i></i><i></i><i class="on"></i><i></i><i></i></div>
</section>

<section class="about">
  <div class="about-backdrop" role="img" aria-label="Decorative yellow and orange circle behind the portrait"></div>
  <div class="about-photo" role="img" aria-label="Portrait photo of the agency owner, Marla Dunbevy"></div>
  <div class="about-text">
    <span class="eyebrow">ABOUT ME</span>
    <h2>MARLA DUNBEVY</h2>
    <p class="role">Agency Owner</p>
    <p class="bio">Marla has been traveling full time for the passed two years and has been very passionate about travel from a young age. Marla is dedicated to working closely with clients to book their dream vacation. Marla's specializations include honeymoons and anniversaries focusing on travel in Europe, Hawaii and all inclusive resorts in the Caribbean.</p>
    <span class="btn">READ MORE</span>
  </div>
</section>

<section class="packages">
  <h2 class="heading" style="top:40px">HOLIDAY PACKAGES</h2>
  <div class="pkg pkg-hawaii" role="img" aria-label="Hawaii beachfront hotels along a curved bay at dusk">
    <span class="pkg-label">HAWAII</span>
    <span class="pkg-badge"><svg width="40" height="34" viewBox="0 0 40 34" fill="none" stroke="#e8603c" stroke-width="2"><path d="M4 14 L20 2 L36 14Z"/><path d="M9 14v18M31 14v18M15 20h10v12H15z"/></svg></span>
  </div>
  <div class="pkg pkg-europe" role="img" aria-label="Paris iron tower beside a stone bridge">
    <span class="pkg-label">EUROPE</span>
    <span class="pkg-badge"><svg width="30" height="36" viewBox="0 0 30 36" fill="none" stroke="#e8603c" stroke-width="2"><path d="M15 1v6M12 7h6l2 12h-10zM10 19h10l5 16H5z"/><path d="M11 35a4 4 0 0 1 8 0"/></svg></span>
  </div>
  <div class="pkg pkg-carib" role="img" aria-label="Caribbean coastline with resort villas at sunset">
    <span class="pkg-label">CARIBBEAN</span>
    <span class="pkg-badge"><svg width="40" height="34" viewBox="0 0 40 34" fill="none" stroke="#e8603c" stroke-width="2"><path d="M16 30 C18 20 18 12 14 6M14 6c-6-2-10 2-11 6M14 6c4-4 10-3 12 1M2 30h36M6 34h28"/><circle cx="31" cy="14" r="4"/></svg></span>
  </div>
</section>

<section class="offers">
  <h2 class="heading" style="top:52px">BEST OFFERS EXCLUSIVELY FOR YOU!</h2>
  <div class="tile t1" role="img" aria-label="Wooden pier over turquoise water leading to an overwater hut">
    <div style="position:absolute;left:22px;top:14px">
      <div style="font-size:20px;font-weight:500;padding-left:34px">LUXURY</div>
      <div class="script">Vacation</div>
      <span class="tag" style="margin-left:50px;margin-top:6px">BOOK NOW</span>
    </div>
  </div>
  <div class="tile t2" role="img" aria-label="Gothic castle towers above a city at golden hour">
    <div style="position:absolute;left:18px;top:200px">
      <div class="script">Best</div>
      <h3>DEALS</h3>
      <p>Lorem ipsum dolor sit amet</p>
      <span class="tag" style="margin-top:6px">BOOK NOW</span>
    </div>
  </div>
  <div class="tile t3" role="img" aria-label="Aerial view of a palm-lined island beach and turquoise lagoon">
    <div style="position:absolute;left:268px;top:118px;color:#1b1b1b">
      <div class="script" style="color:#fff">Best</div>
      <h3 style="color:#1b1b1b">CARIBBEAN<br>HOLIDAY</h3>
      <span class="price" style="margin-top:10px">$1100.00</span><br>
      <span class="tag" style="margin-top:8px">BOOK NOW</span>
    </div>
  </div>
  <div class="tile t4" role="img" aria-label="Paris iron tower above riverside trees under a blue sky">
    <div style="position:absolute;left:36px;top:30px;color:#1b1b1b">
      <h3 style="color:#1b1b1b">PARIS<br>HOLIDAY</h3>
      <p style="margin-top:12px;color:#1b1b1b">Lorem ipsum dolor sit amet</p>
      <span class="price" style="margin-top:18px">$850.00</span><br>
      <span class="tag" style="margin-top:8px">BOOK NOW</span>
    </div>
  </div>
  <div class="tile t5" role="img" aria-label="Triumphal stone arch under a pastel sky">
    <div style="position:absolute;left:18px;top:18px">
      <p style="font-size:17px;color:#1b1b1b">LOREM IPSUM</p>
      <span class="tag" style="margin-top:6px">BOOK NOW</span>
    </div>
  </div>
  <div class="tile t6" role="img" aria-label="Leaning palm tree over a white sand beach">
    <div style="position:absolute;left:20px;top:240px;color:#1b1b1b">
      <p style="font-size:17px;color:#1b1b1b">LOREM IPSUM</p>
      <p style="font-size:13px;color:#1b1b1b">Lorem ipsum dolor sit amet</p>
      <span class="tag" style="margin-top:6px">BOOK NOW</span>
    </div>
  </div>
</section>

<section class="testimonials" role="img" aria-label="Faded coastal landscape backdrop">
  <h2 class="heading" style="top:40px">TESTIMONIALS</h2>
  <article class="quote-card" style="left:131px">
    <div class="quote-mark">&ldquo;</div>
    <p>Sed ut perspiciatis unde omnis iste natus error sit voluptatem accusantium doloremque laudantium, totam rem aperi am, eaque ipsa quae ab illo inventore veritatis et quasi architecto beatae vitae dicta sunt explicabo. Nemo enim ipsam voluptatem quia voluptas sit aspernatur aut odit aut fugit,</p>
    <div class="who">RICHARD<span>England</span></div>
  </article>
  <article class="quote-card" style="left:456px">
    <div class="quote-mark">&ldquo;</div>
    <p>Sed ut perspiciatis unde omnis iste natus error sit voluptatem accusantium doloremque laudantium, totam rem aperi am, eaque ipsa quae ab illo inventore veritatis et quasi architecto beatae vitae dicta sunt explicabo. Nemo enim ipsam voluptatem quia voluptas sit aspernatur aut odit aut fugit,</p>
    <div class="who">RICHARD<span>England</span></div>
  </article>
  <article class="quote-card" style="left:774px">
    <div class="quote-mark">&ldquo;</div>
    <p>Sed ut perspiciatis unde omnis iste natus error sit voluptatem accusantium doloremque laudantium, totam rem aperi am, eaque ipsa quae ab illo inventore veritatis et quasi architecto beatae vitae dicta sunt explicabo. Nemo enim ipsam voluptatem quia voluptas sit aspernatur aut odit aut fugit,</p>
    <div class="who">RICHARD<span>England</span></div>
  </article>
</section>

<section class="features">
  <div class="feature" style="left:85px">
    <div class="icon"><svg width="54" height="54" viewBox="0 0 54 54" fill="none" stroke="#f0b94a" stroke-width="3"><circle cx="30" cy="14" r="10" fill="#f0b94a"/><path d="M4 36h8l10 4h10a3 3 0 0 0 0-6H22M12 46l10 4 24-10a3 3 0 0 0-3-5l-11 4"/></svg></div>
    <h4>BEST PRICE GUARANTEE</h4>
    <p>Sed ut perspiciatis unde omnis iste natus error sit voluptatem accus antium doloremque laudantium, totam rem aperi am.</p>
  </div>
  <div class="feature" style="left:440px">
    <div class="icon"><svg width="50" height="56" viewBox="0 0 50 56" fill="none" stroke="#f0b94a" stroke-width="3"><path d="M25 3 L46 11v16c0 14-10 23-21 27C14 50 4 41 4 27V11z"/><circle cx="25" cy="28" r="10" fill="#f0b94a"/><path d="M20 28l4 4 7-8" stroke="#fff"/></svg></div>
    <h4>SAFE AND SECURE</h4>
    <p>Sed ut perspiciatis unde omnis iste natus error sit voluptatem accus antium doloremque laudantium, totam rem aperi am.</p>
  </div>
  <div class="feature" style="left:800px">
    <div class="icon"><svg width="52" height="52" viewBox="0 0 52 52" fill="#f0b94a"><rect x="4" y="22" width="10" height="26"/><path d="M18 22 L28 4c5 0 6 4 5 9l-2 8h14a4 4 0 0 1 4 5l-4 18a4 4 0 0 1-4 4H18z"/></svg></div>
    <h4>BEST TRAVEL AGENTS</h4>
    <p>Sed ut perspiciatis unde omnis iste natus error sit voluptatem accus antium doloremque laudantium, totam rem aperi am.</p>
  </div>
</section>

<section class="contact">
  <h2 class="heading" style="top:47px">CONTACT US</h2>
  <div class="field" style="left:292px;top:145px;width:302px;height:45px">NAME</div>
  <div class="field" style="left:607px;top:145px;width:301px;height:45px">EMAIL</div>
  <div class="field" style="left:292px;top:206px;width:302px;height:46px">PHONE</div>
  <div class="field" style="left:607px;top:206px;width:301px;height:46px">SUBJECT</div>
  <div class="field" style="left:292px;top:266px;width:616px;height:124px">MESSAGE</div>
  <span class="btn">SUBMIT</span>
</section>

<footer class="site-footer">
  <div class="brand" style="left:130px;top:44px">
    <span class="brand-dot" style="width:40px;height:40px"></span>
    <span class="brand-name">Harbors &amp; Hammocks<small>TRAVEL AGENCY</small></span>
  </div>
  <div class="follow" style="left:527px;top:51px">FOLLOW US <span class="dot" style="margin-left:4px"></span><span class="dot"></span><span class="dot"></span></div>
  <div class="mail">
    <svg width="18" height="14" viewBox="0 0 18 14" fill="none" stroke="#1b1b1b" stroke-width="1.4" style="margin-top:6px"><rect x="1" y="1" width="16" height="12"/><path d="M1 1l8 7 8-7"/></svg>
    <p>EMAIL US<strong>marla@harborsandhammockstravel.example</strong></p>
  </div>
  <nav class="footer-nav">
    <span style="left:525px">ABOUT US</span>
    <span style="left:631px">CONSULTATION</span>
    <span style="left:767px">TOUR PACKAGES</span>
    <span style="left:916px">BLOG</span>
    <span style="left:980px">CONTACT US</span>
  </nav>
  <div class="rule"></div>
  <p class="copy">Copyright &copy; 2021 All Rights Reserved</p>
</footer>

</body>
</html>
```